Heavy Duty Repairs Poster

Good afternoon - I'm looking for a poster , design to set up around different areas. The Poster must consist of the following
- Heavy duty repairs
- Pictures of Semi trucks , heavy construction equipment , trailers
- Agriculture
- All north American equipment ( see attached pictures)
- Brief Descriptions in bullet point forms
CVIPS
WELDING
AIR CONDITIONING
ENGINE REBUILDS
DIAGONSTICS
FLEET MANAGMENT
TIRE REPAIR AND SALES
ELECTRICAL , HYDRALIC , POWER TRAIN SERVICE AND REPAIRS
PART SALES
FLEET MAINTINACE
DELTEING AND TUNING
AFTER MARKET INSTALLS OUTFITTING
ONSITE & OFFSITE REPAIRS
FULL RECERTIFACTION OVERHAULING
Warranty Approved

Target Market(s)

Heavy Duty Truck , Equipment , Agriculture Owners

Industry/Entity Type

Heavy Duty Repairs

Colors
EB3D1F
EC4F4E
F09395
F8D3D4
FCEDEE

Requirements
Must have
• Pictures of : Semi trucks and trailer , Construction heavy equipment , agriculture equipment
Nice to have
• Flashy and stands out

```html
<!DOCTYPE html>
<html lang="en">
<head>
<meta charset="UTF-8">
<title>Ridgeline Mechanical Services – Heavy Duty Repairs</title>
<link rel="stylesheet" href="https://fonts.googleapis.com/css2?family=Inter:ital,wght@0,400;0,700;0,800;1,800&family=Great+Vibes&display=swap">
<style>
  :root{
    --red:#ED1C24;
    --red-deep:#B3121A;
    --ink:#0E0E0F;
    --ink-soft:#1E1E20;
    --white:#FFFFFF;
    --dozer:#E8C33A;
    --dozer-deep:#9C7E1C;
  }
  *{margin:0;padding:0;box-sizing:border-box}
  html,body{width:973px;height:1200px;overflow:hidden;background:var(--ink)}
  .poster{
    position:relative;width:973px;height:1200px;overflow:hidden;
    background:
      radial-gradient(ellipse at 30% 20%, #2a2a2c 0%, transparent 60%),
      radial-gradient(ellipse at 80% 70%, #242426 0%, transparent 55%),
      linear-gradient(160deg, var(--ink-soft) 0%, var(--ink) 100%);
    font-family:"Inter",Arial,sans-serif;color:var(--white);
  }
  .brand{position:absolute;left:0;top:100px;width:622px;text-align:center}
  .brand-name{font-weight:700;font-size:30px;letter-spacing:-0.5px;color:var(--white)}
  .brand-place{font-weight:700;font-size:22px;margin-top:8px;color:var(--white)}
  .hero-band{position:absolute;left:0;top:242px;width:670px;height:172px}
  .hero-text{position:absolute;left:60px;top:280px;font-style:italic;font-weight:800;letter-spacing:-1.2px;line-height:1.05}
  .hero-text .lead{font-size:34px;display:block}
  .hero-text .rest{font-size:28px;display:block}
  .photo-dozer{position:absolute;left:468px;top:142px;width:505px;height:339px;
    background:linear-gradient(150deg,var(--dozer) 0%,#d9ae28 55%,var(--dozer-deep) 100%);
    clip-path:polygon(55% 0,100% 8%,100% 72%,60% 100%,0 82%,6% 50%,25% 40%)}
  .services-title{position:absolute;left:60px;top:456px;font-size:74px;font-weight:800;letter-spacing:-2.5px;line-height:1.1}
  .services{position:absolute;top:556px;list-style:none}
  .services.col-a{left:64px}
  .services.col-b{left:423px}
  .services li{display:flex;align-items:center;height:35px;font-size:26.5px;letter-spacing:-0.8px;white-space:nowrap}
  .services svg{width:30px;height:28px;margin-right:14px;flex:none}
  .photo-truck{position:absolute;left:0;top:839px;width:561px;height:354px;
    background:linear-gradient(160deg,#e0232b 0%,#a5141a 55%,#5a5c60 100%);
    clip-path:polygon(10% 0,55% 4%,78% 30%,100% 40%,100% 100%,0 100%,0 20%)}
  .warranty{position:absolute;left:470px;top:858px;width:450px;font-family:"Great Vibes",cursive;font-size:64px;line-height:1;color:var(--red);transform:rotate(-4deg);transform-origin:left center;white-space:nowrap}
  .call-band{position:absolute;left:559px;top:1079px;width:414px;height:59px;background:var(--red);display:flex;align-items:center;padding-left:32px;font-weight:700;font-size:26px;letter-spacing:-0.6px;white-space:nowrap}
  .call-band svg{width:28px;height:28px;margin-right:14px;flex:none}
</style>
</head>
<body>
<main class="poster">
  <svg width="0" height="0" style="position:absolute">
    <symbol id="wrench" viewBox="0 0 32 30">
      <path d="M27 3a7 7 0 0 0-8.6 8.8L4 26.2a2 2 0 0 0 2.8 2.8l14.4-14.4A7 7 0 0 0 30 6l-4 4-4-1-1-4z" fill="none" stroke="#ED1C24" stroke-width="2.2" stroke-linejoin="round"/>
    </symbol>
  </svg>

  <header class="brand">
    <div class="brand-name">Ridgeline Mechanical Services</div>
    <div class="brand-place">Pinecrest , Alberta</div>
  </header>

  <svg class="hero-band" viewBox="0 0 670 172" preserveAspectRatio="none">
    <polygon points="0,0 670,0 497,172 0,172" fill="#ED1C24"/>
  </svg>
  <p class="hero-text">
    <span class="lead">RIDGELINE MECHANICAL</span>
    <span class="rest">is your One Stop shop for</span>
    <span class="rest">all your mechanical needs.</span>
  </p>

  <div class="photo-dozer" role="img" aria-label="Yellow crawler bulldozer with front blade"></div>

  <h2 class="services-title">Our Services</h2>
  <ul class="services col-a">
    <li><svg><use href="#wrench"/></svg>C.V.I.P.S</li>
    <li><svg><use href="#wrench"/></svg>Welding</li>
    <li><svg><use href="#wrench"/></svg>Part Sales</li>
    <li><svg><use href="#wrench"/></svg>Diagnostics</li>
    <li><svg><use href="#wrench"/></svg>Delting &amp; Tuning</li>
    <li><svg><use href="#wrench"/></svg>Engine Rebuilds</li>
    <li><svg><use href="#wrench"/></svg>Air Condiotioning</li>
  </ul>
  <ul class="services col-b">
    <li><svg><use href="#wrench"/></svg>Tire Repair &amp; Sales</li>
    <li><svg><use href="#wrench"/></svg>Power Train Service</li>
    <li><svg><use href="#wrench"/></svg>Onsite &amp; Offsite Repairs</li>
    <li><svg><use href="#wrench"/></svg>After Market Installs Outfitting</li>
    <li><svg><use href="#wrench"/></svg>Electrical &amp; Hydraulic Repairs</li>
    <li><svg><use href="#wrench"/></svg>Full Recertifaction Overhauling</li>
    <li><svg><use href="#wrench"/></svg>Fleet management &amp; Maintenance</li>
  </ul>

  <div class="photo-truck" role="img" aria-label="Red semi truck tractor with chrome grille and stacks"></div>

  <p class="warranty">Warranty Approved</p>

  <div class="call-band">
    <svg viewBox="0 0 24 24"><path d="M6.6 2.5l3 3.2-1.8 2.6a13 13 0 0 0 7.9 7.9l2.6-1.8 3.2 3-2.2 3.1C11 20 4 13 3.5 4.7z" fill="none" stroke="#fff" stroke-width="2" stroke-linejoin="round"/></svg>
    Call Us: 555-014-2270
  </div>
</main>
</body>
</html>
```